Healthcare and Professional IT Services Company need a redesigned business card

We are a IT Services company that targets small medical practices and professional business such as Attorneys, Accounts, Architects etc. We want to communicate a professional yet friendly image using recent logo redesign here on ArtHarbor. Like to see the colors blue and orange in the design. Must use the Tall Pine Computing as displayed in the new logo - then also want to incorporate the fish logo as well.

Target Market(s)

Small medical and professional services

Industry/Entity Type

It Company

Contact Information for Business Card

The usual stuff, place for name address phone website. Also maybe our tagline which is "hooked on technology"

Requirements
Must have
• My new logo and the fish somewhere on the card

```html
<!DOCTYPE html>
<html lang="en">
<head>
<meta charset="utf-8">
<title>Tall Pine Computing – Business Card</title>
<link rel="stylesheet" href="https://fonts.googleapis.com/css2?family=Open+Sans:wght@300;400;600&display=swap">
<style>
  :root {
    --bg: #e9e6e1;
    --paper: #fbfbfb;
    --sky: #45c3ec;
    --band-light: #7fd0e6;
    --band-deep: #4f82c8;
    --name-blue: #5b9bd5;
    --ink: #1c1c1c;
    --rule: #9fb6d6;
    --mark: #e9843f;
  }
  * { box-sizing: border-box; margin: 0; padding: 0; }
  html, body {
    width: 1200px; height: 892px; overflow: hidden;
    background: var(--bg);
    font-family: "Open Sans", Arial, sans-serif;
  }
  .canvas { position: relative; width: 1200px; height: 892px; }

  .card {
    position: absolute; top: 291px;
    width: 540px; height: 310px;
    background: var(--paper);
    box-shadow: 0 6px 18px rgba(0,0,0,.18);
    overflow: hidden;
  }
  .card--back { left: 40px; }
  .card--front { left: 620px; }

  .brand-dot {
    display: block; flex: none;
    border-radius: 50%;
    background: var(--mark);
  }
  .brand-name {
    font-weight: 600; color: var(--sky);
    line-height: 1.1; letter-spacing: -.3px;
    white-space: nowrap;
  }

  /* Back: centred lockup */
  .brand-lockup {
    position: absolute; left: 0; right: 0; top: 124px;
    display: flex; align-items: center; justify-content: center; gap: 16px;
  }
  .brand-lockup .brand-dot { width: 44px; height: 44px; }
  .brand-lockup .brand-name { font-size: 32px; }

  /* Front */
  .front-logo {
    position: absolute; top: 40px; right: 36px;
    display: flex; align-items: center; gap: 12px;
  }
  .front-logo .brand-dot { width: 32px; height: 32px; }
  .front-logo .brand-name { font-size: 24px; }

  .person-name {
    position: absolute; left: 36px; top: 150px;
    font-weight: 300; font-size: 28px; color: var(--name-blue);
    white-space: nowrap;
  }
  .divider {
    position: absolute; left: 276px; top: 138px;
    width: 1px; height: 90px; background: var(--rule);
  }
  .contact {
    position: absolute; left: 296px; top: 140px;
    list-style: none;
    font-size: 14px; color: var(--ink);
  }
  .contact li { display: flex; align-items: center; gap: 10px; height: 26px; white-space: nowrap; }
  .contact svg { width: 16px; height: 16px; flex: none; }

  .band {
    position: absolute; left: 0; right: 0; bottom: 0; height: 46px;
  }
  .band__line {
    position: absolute; left: 0; right: 0; top: 0; height: 5px;
    background: var(--band-deep);
  }
  .band__fill {
    position: absolute; left: 0; right: 0; top: 11px; bottom: 0;
    background: linear-gradient(90deg, var(--band-light), var(--sky));
  }
</style>
</head>
<body>
<main class="canvas">

  <section class="card card--back" aria-label="Card back">
    <div class="brand-lockup">
      <span class="brand-dot" aria-hidden="true"></span>
      <span class="brand-name">Tall Pine Computing</span>
    </div>
  </section>

  <section class="card card--front" aria-label="Card front">
    <div class="front-logo">
      <span class="brand-dot" aria-hidden="true"></span>
      <span class="brand-name">Tall Pine Computing</span>
    </div>

    <p class="person-name">Martin Ellery</p>
    <span class="divider"></span>

    <ul class="contact">
      <li>
        <svg viewBox="0 0 16 16" aria-hidden="true"><rect width="16" height="16" rx="2" fill="#1c1c1c"/><path d="M5 3.5l2 2-1 1.2c.6 1.4 1.6 2.4 3 3l1.2-1 2 2-1.2 1.6C7.5 12 4 8.5 3.6 4.8z" fill="#fff"/></svg>
        +1 555 014 2287
      </li>
      <li>
        <svg viewBox="0 0 16 16" aria-hidden="true"><rect width="16" height="16" rx="2" fill="#1c1c1c"/><circle cx="8" cy="8" r="4.5" fill="none" stroke="#fff" stroke-width="1.2"/><path d="M3.5 8h9M8 3.5c-2 2.5-2 6.5 0 9M8 3.5c2 2.5 2 6.5 0 9" fill="none" stroke="#fff" stroke-width="1"/></svg>
        www.tallpinecomputing.com
      </li>
      <li>
        <svg viewBox="0 0 16 16" aria-hidden="true"><rect width="16" height="16" rx="2" fill="#1c1c1c"/><path d="M8 13s-3.5-4-3.5-6.3a3.5 3.5 0 017 0C11.5 9 8 13 8 13z" fill="#fff"/><circle cx="8" cy="6.6" r="1.3" fill="#1c1c1c"/></svg>
        4820 Cedar Row, Brookfield, ON
      </li>
    </ul>

    <div class="band">
      <span class="band__line"></span>
      <span class="band__fill"></span>
    </div>
  </section>

</main>
</body>
</html>
```